Firm-Asset: Tomorrow - EU-funded management consulting

A website to inform possible customers about my management consulting services for small and medium sized companies. I am using a funding for small and medium companies to do 10 days of workshops and coaching about leadership, further education and employee's health. The Funding is called "Betriebsgut Zukunft" which means something like: Humans are the value of the company. The official logo is attached as a

Target Market(s)

Small and medium sized companies that want to improve their employee's well being and efficiency.

Industry/Entity Type

Management Consulting

Contact Information for Business Card

Malte Quast, Birkenhainweg 14, 10219 Berlin

Logo Text

BetriebsGut Zukunft - Beratung

Font styles to use
Serif
Sans Serif

Requirements
Must have
• a friendly and professional design
Nice to have
• saying somthing about: employees, leadership, further education and employees health are important to us.
Should not have
• should not be too shimmering

```html
<!DOCTYPE html>
<html lang="en">
<head>
<meta charset="utf-8">
<title>Firm-Asset: Tomorrow – Consulting</title>
<link href="https://fonts.googleapis.com/css2?family=Open+Sans:wght@400;600;700&family=Merriweather:wght@400;700&display=swap" rel="stylesheet">
<style>
:root{
  --navy:#0e3a5a;
  --navy-dark:#0a2b44;
  --blue:#1c5f8f;
  --orange:#e38a2c;
  --ink:#3a4047;
  --muted:#7c838a;
  --line:#dde1e5;
  --paper:#ffffff;
  --mist:#eef1f4;
}
*{box-sizing:border-box;margin:0;padding:0}
html,body{width:688px;height:1200px;overflow:hidden}
body{font-family:"Open Sans",Arial,sans-serif;color:var(--ink);background:var(--paper);font-size:8px;line-height:1.5}
.serif{font-family:"Merriweather",Georgia,serif}

.site-header{height:52px;display:flex;align-items:center;justify-content:space-between;padding:0 58px 0 30px}
.brand{display:flex;align-items:center;gap:6px}
.brand-mark{width:16px;height:16px;background:var(--blue)}
.brand-name{font-weight:700;font-size:10px;line-height:1.1;color:var(--navy)}
.main-nav{display:flex;gap:2px}
.main-nav a{font-size:7px;font-weight:600;color:var(--ink);text-decoration:none;padding:7px 8px;letter-spacing:.3px}
.main-nav a.active{background:var(--orange);color:#fff}

.hero{height:330px;background:linear-gradient(#f6f7f9,#e3e7eb);position:relative}
.hero-photo{position:absolute;left:62px;top:14px;width:562px;height:296px;border-radius:10px;border:4px solid #fff;background:linear-gradient(100deg,#e9f1f8 0%,#c4d8e8 30%,#8fb0c9 55%,#3f4c5a 80%,#232a33 100%);box-shadow:0 2px 6px rgba(0,0,0,.15)}
.hero-caption{position:absolute;left:52px;top:210px;background:var(--blue);color:#fff;font-size:15px;line-height:1.3;padding:8px 14px 8px 20px;width:230px;text-transform:uppercase}
.hero-dots{position:absolute;left:322px;top:298px;display:flex;gap:4px}
.hero-dots span{width:5px;height:5px;border-radius:50%;background:#fff;opacity:.8}
.hero-dots span.on{background:var(--orange);opacity:1}

.welcome{display:flex;padding:18px 62px 0 62px;gap:18px;height:175px}
.welcome-text{flex:1}
.welcome h1{font-size:15px;font-weight:400;color:var(--ink);text-transform:uppercase;padding-bottom:6px;border-bottom:1px solid var(--line);margin-bottom:8px}
.welcome p{font-size:6.5px;color:var(--muted);line-height:1.65}
.btn-more{display:inline-block;margin-top:10px;background:var(--navy);color:#fff;font-size:6px;font-weight:700;padding:5px 10px}
.welcome-photo{width:86px;height:150px;background:linear-gradient(#ffffff 0%,#f1f2f3 25%,#2c3440 50%,#1d232b 100%)}

.features{display:flex;padding:4px 62px;gap:14px;height:118px}
.feature{flex:1;text-align:center}
.feature svg{width:26px;height:26px;display:block;margin:0 auto 6px}
.feature h3{font-size:8px;font-weight:700;color:var(--navy);text-transform:uppercase;padding-bottom:4px;border-bottom:1px solid var(--line);margin-bottom:5px}
.feature p{font-size:6px;color:var(--muted)}

.care-band{height:52px;background:var(--navy);display:flex;align-items:center;justify-content:center;gap:8px;color:#fff;font-size:14px}
.care-band svg{width:14px;height:14px}

.news{padding:14px 62px 0;height:169px;background:var(--mist)}
.news h2{font-size:10px;font-weight:700;color:var(--navy);text-transform:uppercase;margin-bottom:8px;border-bottom:1px solid var(--line);padding-bottom:4px}
.news-grid{display:flex;gap:12px}
.news-item{flex:1}
.news-thumb{height:66px}
.t1{background:linear-gradient(135deg,#7fa6c6,#e8eef3 55%,#3b5d7c)}
.t2{background:linear-gradient(135deg,#f2e6da,#b89a83 50%,#4b5563)}
.t3{background:linear-gradient(135deg,#4c6a86,#dfe7ee 50%,#8fa9bf)}
.t4{background:linear-gradient(135deg,#eef3f7,#b7cde0 50%,#6f8fac)}
.news-date{font-size:6.5px;font-weight:700;color:var(--orange);margin-top:5px}
.news-item p{font-size:5.5px;color:var(--muted)}

.partners{height:60px;display:flex;align-items:center;justify-content:space-between;padding:0 62px}
.partners span{width:50px;height:14px;background:#b9c0c7;border-radius:2px}
.partners span:nth-child(2n){width:38px;height:12px;border-radius:50%}

.site-footer{background:var(--navy);height:230px;padding:18px 62px 0;display:flex;gap:18px;color:#cdd8e2}
.site-footer h4{font-size:7px;font-weight:700;color:#fff;text-transform:uppercase;margin-bottom:6px;padding-bottom:4px;border-bottom:1px solid rgba(255,255,255,.2)}
.col{flex:1}
.links{display:flex;gap:10px}
.links ul{list-style:none}
.links li{font-size:6px;line-height:2}
.field{height:16px;background:#fff;margin-bottom:5px;font-size:6px;color:#999;padding:3px 5px}
.btn-sub{display:inline-block;background:var(--orange);color:#fff;font-size:6px;font-weight:700;padding:4px 10px}
.contact-line{display:flex;gap:5px;align-items:flex-start;font-size:6px;margin-bottom:6px}
.contact-line i{flex:none;width:8px;height:8px;border-radius:50%;background:var(--orange)}
.map{height:70px;background:linear-gradient(135deg,#e9e4d4,#cfe0c4 45%,#a9c8de)}

.bottom-bar{height:14px;background:var(--navy-dark);display:flex;align-items:center;justify-content:space-between;padding:0 62px;color:#8fa3b5;font-size:5px}
.social{display:flex;gap:3px}
.social span{width:8px;height:8px;background:var(--blue)}
</style>
</head>
<body>

<header class="site-header">
  <div class="brand">
    <span class="brand-mark"></span>
    <span class="brand-name">BetriebsGut<br>Zukunft</span>
  </div>
  <nav class="main-nav">
    <a class="active" href="#">HOME</a><a href="#">ABOUT</a><a href="#">SERVICES</a><a href="#">PROJECTS</a><a href="#">OUR BLOG</a><a href="#">CONTACT US</a>
  </nav>
</header>

<section class="hero">
  <div class="hero-photo" role="img" aria-label="Consultant in a suit in a bright office with colleagues behind him"></div>
  <div class="hero-caption serif">Conduct workshops on leadership</div>
  <div class="hero-dots"><span class="on"></span><span></span><span></span><span></span></div>
</section>

<section class="welcome">
  <div class="welcome-text">
    <h1 class="serif">Welcome to Betriebsgut Zukunft</h1>
    <p>We help small and medium sized companies grow by investing in their people. Our funded programme offers ten days of workshops and coaching on leadership, further education and employee health. Together with your team we look at daily work, find what holds people back and build simple habits that last.</p>
    <p>Every programme starts with a short talk about your goals. We then plan sessions that fit your business, your staff and your time. The funding covers a large part of the costs, so you can focus on what matters most: the people who make your company strong and keep it healthy.</p>
    <span class="btn-more">READ MORE</span>
  </div>
  <div class="welcome-photo" role="img" aria-label="Portrait of the consultant in a dark suit"></div>
</section>

<section class="features">
  <div class="feature">
    <svg viewBox="0 0 26 26" fill="none" stroke="#e38a2c" stroke-width="1.6"><rect x="3" y="4" width="20" height="13"/><path d="M13 17v5M8 23l5-6 5 6M7 13l4-4 3 3 5-5"/></svg>
    <h3>Workshops</h3>
    <p>Practical sessions for managers and teams on leading people well.</p>
  </div>
  <div class="feature">
    <svg viewBox="0 0 26 26" fill="none" stroke="#e38a2c" stroke-width="1.6"><rect x="3" y="7" width="20" height="15" rx="2"/><path d="M9 7V4h8v3M13 11v7M9.5 14.5h7"/></svg>
    <h3>Employees Health</h3>
    <p>Ideas and routines that keep your staff well, fit and motivated.</p>
  </div>
  <div class="feature">
    <svg viewBox="0 0 26 26" fill="none" stroke="#e38a2c" stroke-width="1.6"><path d="M2 10l11-5 11 5-11 5z"/><path d="M7 12.5v5c3 3 9 3 12 0v-5M23 10v7"/></svg>
    <h3>Education</h3>
    <p>Further training plans that help your people learn and grow.</p>
  </div>
  <div class="feature">
    <svg viewBox="0 0 26 26" fill="none" stroke="#e38a2c" stroke-width="1.6"><circle cx="10" cy="10" r="4"/><circle cx="10" cy="10" r="7" stroke-dasharray="3 2"/><circle cx="19" cy="19" r="2.5"/><circle cx="19" cy="19" r="4.5" stroke-dasharray="2 1.5"/></svg>
    <h3>Support</h3>
    <p>Personal coaching and advice whenever your team needs a hand.</p>
  </div>
</section>

<section class="care-band serif">
  <svg viewBox="0 0 14 14" fill="none" stroke="#e38a2c" stroke-width="2.4"><path d="M2 7l3.5 3.5L12 3"/></svg>
  We care for our employees
</section>

<section class="news">
  <h2>Latest News</h2>
  <div class="news-grid">
    <article class="news-item">
      <div class="news-thumb t1" role="img" aria-label="Business team meeting around a table"></div>
      <div class="news-date">09 AUG, 2015</div>
      <p>New leadership workshop dates for autumn are now open.</p>
    </article>
    <article class="news-item">
      <div class="news-thumb t2" role="img" aria-label="Colleagues working together at laptops"></div>
      <div class="news-date">10 AUG, 2015</div>
      <p>How small firms use funding to train their staff.</p>
    </article>
    <article class="news-item">
      <div class="news-thumb t3" role="img" aria-label="Team giving a presentation in an office"></div>
      <div class="news-date">15 AUG, 2015</div>
      <p>Five simple steps to a healthier working day.</p>
    </article>
    <article class="news-item">
      <div class="news-thumb t4" role="img" aria-label="Group of employees in a bright seminar room"></div>
      <div class="news-date">17 AUG, 2015</div>
      <p>Coaching results from our latest partner company.</p>
    </article>
  </div>
</section>

<section class="partners" aria-label="Partners">
  <span></span><span></span><span></span><span></span><span></span><span></span><span></span>
</section>

<footer class="site-footer">
  <div class="col">
    <h4>Quick Links</h4>
    <div class="links">
      <ul><li>Home</li><li>About Us</li><li>Our Services</li><li>Projects</li><li>Contact Us</li></ul>
      <ul><li>Partners</li><li>Privacy Policy</li><li>Disclaimer</li><li>Sitemap</li><li>Terms</li></ul>
    </div>
  </div>
  <div class="col">
    <h4>Newsletter</h4>
    <div class="field">Name</div>
    <div class="field">Email Address</div>
    <span class="btn-sub">Subscribe</span>
  </div>
  <div class="col">
    <h4>Contact Us</h4>
    <div class="contact-line"><i></i><span>BETRIEBSGUT ZUKUNFT<br>Malte Quast<br>Birkenhainweg 14, 10219 Berlin</span></div>
    <div class="contact-line"><i></i><span>+49 30 555 0142</span></div>
    <div class="contact-line"><i></i><span>info@betriebsgut-zukunft.example</span></div>
  </div>
  <div class="col">
    <h4>Our Location</h4>
    <div class="map" role="img" aria-label="Street map showing the office location in Berlin"></div>
  </div>
</footer>

<div class="bottom-bar">
  <span>© 2015 Betriebsgut Zukunft. All rights reserved.</span>
  <span class="social"><span></span><span></span><span></span><span></span></span>
</div>

</body>
</html>
```